Birch Hauling Business Card Design Project

We need a new company business card. We provide professional timber harvesting (logging) and forest management services. I'm open to any creative design. Most company caps and shirts are navy blue and Light grey. Logo does not necessarily have to contain those colors. Logo containing picture of logging equipment, log truck, trees, or logs are acceptable. Be creative. Final logo should communicate our company's pride and professionalism in the East Texas Timber Industry.
Updates

Target Market(s)

Timber owners, sawmills, and forestry professionals

Industry/Entity Type

Business

Requirements
Must have
• Must have Contact Info.
Phone: 555-402-5917
address: PO Box 4830
Cedar Bend, Tx 75921
www.jmbirchhauling.example
jmbirchhauling@mailbox.example
Owner: Jared Marsh

Or design must leave room for this info.

```html
<!DOCTYPE html>
<html lang="en">
<head>
<meta charset="utf-8">
<title>J.M. Birch Hauling Company – Business Card</title>
<link rel="stylesheet" href="https://fonts.googleapis.com/css2?family=Open+Sans:wght@400;600&display=swap">
<style>
  :root {
    --bg: #e4e4e4;
    --bark: #3b2117;
    --bark-deep: #24130d;
    --leaf: #8cba4f;
    --leaf-line: #7fb23e;
    --paper: #ffffff;
    --ink: #1d1d1d;
    --cream: #f4efe9;
    --muted: #cfc4ba;
  }
  * { box-sizing: border-box; margin: 0; padding: 0; }
  html, body { width: 1200px; height: 864px; overflow: hidden; }
  body {
    background: var(--bg);
    font-family: "Open Sans", Arial, sans-serif;
    position: relative;
  }
  .card {
    position: absolute;
    top: 278px;
    width: 540px;
    height: 308px;
    border-radius: 3px;
    box-shadow: 0 6px 18px rgba(0,0,0,.18);
    overflow: hidden;
  }
  /* Front side */
  .card-front {
    left: 40px;
    background: radial-gradient(ellipse at 45% 30%, #4a2a1d 0%, var(--bark) 45%, var(--bark-deep) 100%);
    color: var(--cream);
  }
  .card-front .company-name {
    position: absolute;
    top: 52px; left: 0; right: 0;
    text-align: center;
    font-size: 25px;
    font-weight: 400;
    color: #fff;
  }
  .owner {
    position: absolute;
    left: 34px; top: 128px;
  }
  .owner-name { font-size: 15px; letter-spacing: .4px; color: #fff; }
  .owner-title { font-size: 9px; color: var(--muted); margin-top: -1px; }
  .address {
    position: absolute;
    left: 34px; top: 176px;
    font-size: 11.5px;
    color: var(--cream);
  }
  .divider {
    position: absolute;
    left: 276px; top: 150px;
    width: 1px; height: 84px;
    background: var(--leaf);
  }
  .contact-list {
    position: absolute;
    left: 300px; top: 164px;
    list-style: none;
    font-size: 11.5px;
    line-height: 19px;
  }
  .contact-list li { display: flex; align-items: center; gap: 10px; }
  .contact-list svg { width: 11px; height: 11px; flex: none; }
  .band-rule {
    position: absolute; left: 0; right: 0; top: 252px;
    height: 1px; background: #e8e2dc;
  }
  .band {
    position: absolute; left: 0; right: 0; top: 256px;
    height: 30px; background: var(--leaf);
  }
  /* Back side */
  .card-back {
    left: 620px;
    background: var(--paper);
    display: flex;
    align-items: center;
  }
  .back-title {
    display: flex;
    align-items: center;
    width: 100%;
    gap: 16px;
  }
  .card-back .company-name {
    flex: none;
    color: var(--ink);
    font-size: 26px;
    font-weight: 400;
    white-space: nowrap;
  }
  .accent {
    flex: 1;
    height: 1.5px;
    background: var(--leaf-line);
  }
</style>
</head>
<body>
  <section class="card card-front" aria-label="Business card front">
    <h1 class="company-name">J.M. Birch Hauling Company</h1>
    <div class="owner">
      <div class="owner-name">JARED MARSH</div>
      <div class="owner-title">Owner</div>
    </div>
    <p class="address">PO Box 4830 Cedar Bend, Tx 75921</p>
    <div class="divider"></div>
    <ul class="contact-list">
      <li>
        <svg viewBox="0 0 12 12" aria-hidden="true"><circle cx="6" cy="3.5" r="2.6" fill="#8cba4f"/><path d="M1 12c0-3.2 2.2-5 5-5s5 1.8 5 5z" fill="#8cba4f"/></svg>
        555-402-5917
      </li>
      <li>
        <svg viewBox="0 0 12 12" aria-hidden="true"><circle cx="6" cy="6" r="5" fill="none" stroke="#8cba4f" stroke-width="1.4"/><path d="M1 6h10M6 1c-2.5 3-2.5 7 0 10M6 1c2.5 3 2.5 7 0 10" fill="none" stroke="#8cba4f" stroke-width="1"/></svg>
        www.jmbirchhauling.example
      </li>
      <li>
        <svg viewBox="0 0 12 12" aria-hidden="true"><rect x="0.5" y="2" width="11" height="8" fill="#8cba4f"/><path d="M0.5 2l5.5 4.5L11.5 2" fill="none" stroke="#3b2117" stroke-width="1"/></svg>
        jmbirchhauling@mailbox.example
      </li>
    </ul>
    <div class="band-rule"></div>
    <div class="band"></div>
  </section>

  <section class="card card-back" aria-label="Business card back">
    <div class="back-title">
      <span class="accent"></span>
      <h2 class="company-name">J.M. Birch Hauling Company</h2>
      <span class="accent"></span>
    </div>
  </section>
</body>
</html>
```